TV Antenna Installation business needs a unique flyer

We need a simple but effective flyer design for our TV Aerial installation company based in Newcastle, NSW, Australia called Bright Harbour TV & Aerial Svcs.
We are trying to target areas where there has been a new transmitter installed and most houses just require their aerial redirecting and tv's retuning.

Industry/Entity Type

Business

Requirements
Must have
• We would like the idea of a headline phrase such as " Poor TV reception……..now a thing from the past" or something similar & catchy.
Also "Did you know a new transmitter has been recently installed in your area, we can therefore now GUARANTEE 100% PERFECT PICTURE
Charges from only $95.
- Free 5 year warranty
- Free signal testing
- Free Onsite Quote
Phone 0463 527 209
Nice to have
• Other services include:

- New Installs
- Extra Points & repairs
- TV wall mounting/Home Cinema
- Pull down tall masts

Modern tv picture, see example uploaded

```html
<!DOCTYPE html>
<html lang="en">
<head>
<meta charset="utf-8">
<title>Bright Harbour TV &amp; Aerial Svcs – Flyer</title>
<link href="https://fonts.googleapis.com/css2?family=Arimo:wght@700&family=PT+Sans+Narrow:wght@700&family=Open+Sans:wght@600;700&display=swap" rel="stylesheet">
<style>
  :root {
    --brand-blue: #1b58ae;
    --red: #e5262d;
    --red-light: #ef4b4f;
    --green: #8cc63f;
    --green-dark: #6fae2c;
    --yellow: #ffd21f;
    --orange: #f58a1f;
    --white: #ffffff;
    --ink: #141414;
    --banner-top: #3fa0e6;
    --banner-bottom: #1566b7;
  }
  * { box-sizing: border-box; margin: 0; padding: 0; }
  html, body { width: 948px; height: 1200px; overflow: hidden; background: #f2f2f2; }
  .flyer { position: relative; width: 948px; height: 1200px; overflow: hidden; background: var(--white); }
  .backdrop { position: absolute; inset: 0; }

  .title {
    position: absolute; top: 28px; left: 230px; width: 620px; text-align: center;
    font-family: "Arimo", Arial, sans-serif; font-weight: 700; font-size: 62px;
    line-height: 82px; color: var(--brand-blue);
  }

  .tv-art {
    position: absolute; left: 60px; top: 150px; width: 218px; height: 270px;
    border-radius: 30px; background: linear-gradient(160deg, #f3e36a, #d8b81a);
  }

  .headline {
    position: absolute; left: 407px; top: 262px;
    font-family: "PT Sans Narrow", "Arial Narrow", sans-serif; font-weight: 700;
    font-size: 50px; line-height: 68px; color: var(--white);
    text-shadow: 2px 2px 3px rgba(0,0,0,.35);
  }

  .intro {
    position: absolute; left: 100px; top: 508px; width: 380px; text-align: center;
    font-family: "Open Sans", Arial, sans-serif; font-weight: 600;
    font-size: 22px; line-height: 39px; color: var(--white);
  }

  .services { position: absolute; left: 451px; top: 468px; width: 410px; text-align: center; }
  .services-heading {
    font-family: "PT Sans Narrow", "Arial Narrow", sans-serif; font-weight: 700;
    font-size: 36px; letter-spacing: 2px; color: var(--yellow); line-height: 44px;
  }
  .services-list { list-style: none; border-top: 2px solid var(--white); }
  .services-list li {
    font-family: "Open Sans", Arial, sans-serif; font-weight: 600; font-size: 23px;
    color: var(--white); line-height: 38px; border-bottom: 2px solid var(--white);
  }

  .guarantee {
    position: absolute; left: 110px; top: 680px; width: 216px; height: 216px; border-radius: 50%;
    background: radial-gradient(circle at 40% 35%, #fbf7a0, #e6e21e 70%);
    border: 8px solid var(--red); box-shadow: 0 0 0 4px #7a1a1a, 4px 6px 10px rgba(0,0,0,.35);
    display: flex; align-items: center; justify-content: center; text-align: center;
    font-family: "Arimo", Arial, sans-serif; font-weight: 700; font-size: 27px;
    line-height: 35px; color: var(--ink);
  }

  .price-rule { position: absolute; left: 497px; top: 752px; width: 520px; height: 3px; background: #c9a84a; left: 498px; width: 518px; }
  .price-banner {
    position: absolute; left: 444px; top: 717px; width: 422px; height: 72px;
    background: linear-gradient(var(--banner-top), var(--banner-bottom));
    border-radius: 6px; box-shadow: 3px 5px 8px rgba(0,0,0,.35);
    font-family: "PT Sans Narrow", "Arial Narrow", sans-serif; font-weight: 700;
    font-size: 40px; line-height: 72px; text-align: center; color: var(--white);
  }

  .call {
    position: absolute; left: 431px; top: 800px; white-space: nowrap;
    font-family: "Arimo", Arial, sans-serif; font-weight: 700; color: var(--white);
    text-shadow: 2px 2px 4px rgba(0,0,0,.4);
  }
  .call-label { font-size: 40px; }
  .call-number { font-size: 54px; }

  .location {
    position: absolute; left: 60px; top: 918px; width: 364px; text-align: center;
    font-family: "Open Sans", Arial, sans-serif; font-weight: 700; font-size: 24px; color: var(--ink);
  }

  .room-photo {
    position: absolute; left: 69px; top: 958px; width: 353px; height: 196px; border-radius: 10px;
    background: linear-gradient(135deg, #f4e6c4, #c9a468 55%, #4a3220);
    border: 3px solid var(--white);
  }
  .photo-caption {
    position: absolute; left: 69px; top: 1158px; width: 353px; text-align: center;
    font-family: "Open Sans", Arial, sans-serif; font-weight: 600; font-size: 8.5px;
    line-height: 11px; color: var(--ink);
  }

  .perks { position: absolute; left: 460px; top: 1010px; list-style: none; }
  .perks li {
    position: relative; padding-left: 44px;
    font-family: "PT Sans Narrow", "Arial Narrow", sans-serif; font-weight: 700;
    font-size: 40px; line-height: 51px; color: var(--white);
    text-shadow: 2px 2px 3px rgba(0,0,0,.45);
  }
  .perks li::before {
    content: ""; position: absolute; left: 4px; top: 17px; width: 20px; height: 20px;
    border-radius: 50%; background: var(--ink);
  }
</style>
</head>
<body>
<main class="flyer">
  <svg class="backdrop" width="948" height="1200" viewBox="0 0 948 1200" aria-hidden="true">
    <defs>
      <linearGradient id="redFill" x1="0" y1="0" x2="1" y2="0">
        <stop offset="0" stop-color="var(--red)"/>
        <stop offset="1" stop-color="var(--red-light)"/>
      </linearGradient>
      <linearGradient id="greenFill" x1="0" y1="0" x2="1" y2="1">
        <stop offset="0" stop-color="#a9d65a"/>
        <stop offset="1" stop-color="var(--green-dark)"/>
      </linearGradient>
    </defs>
    <rect class="base" width="948" height="1200" fill="#ffffff"/>
    <path class="green-field" d="M0,520 C250,760 600,930 948,950 L948,1200 L0,1200 Z" fill="url(#greenFill)"/>
    <!-- top swoosh bands -->
    <path d="M0,40 C260,110 600,270 948,230 L948,300 C600,330 260,200 0,120 Z" fill="var(--green)"/>
    <path d="M0,60 C260,130 600,285 948,262 L948,300 C600,330 260,200 0,120 Z" fill="var(--yellow)"/>
    <path d="M0,78 C260,150 600,295 948,278 L948,300 C600,330 260,200 0,120 Z" fill="var(--orange)"/>
    <!-- lower swoosh bands -->
    <path d="M0,500 C250,740 600,905 948,920 L948,975 C600,960 250,800 0,600 Z" fill="var(--yellow)"/>
    <path d="M0,520 C250,760 600,925 948,938 L948,975 C600,960 250,800 0,600 Z" fill="var(--orange)"/>
    <path d="M0,538 C250,778 600,940 948,952 L948,975 C600,960 250,800 0,600 Z" fill="var(--white)"/>
    <path class="red-field" d="M0,96 C260,168 600,310 948,292 L948,962 C600,950 250,790 0,556 Z" fill="url(#redFill)"/>
  </svg>

  <h1 class="title">Bright Harbour TV &amp;<br>Aerial Svcs</h1>

  <div class="tv-art" role="img" aria-label="Illustration of a yellow retro television with antennas and a signal line on the screen"></div>

  <h2 class="headline">Poor TV Reception?<br>Now a thing from the Past.</h2>

  <p class="intro">Did you know a new transmitter has been recently installed in your area, we can therefore NOW</p>

  <section class="services">
    <h3 class="services-heading">OUR SERVICES:</h3>
    <ul class="services-list">
      <li>New Installs</li>
      <li>Extra Points &amp; repairs</li>
      <li>TV wall mounting/Home Cinema</li>
      <li>Pull down tall masts</li>
    </ul>
  </section>

  <div class="guarantee">GUARANTEE<br>100%<br>PERFECT<br>PICTURE</div>

  <div class="price-rule"></div>
  <div class="price-banner">Charges from only $95</div>

  <p class="call"><span class="call-label">Call: </span><span class="call-number">0463 527 209</span></p>

  <p class="location">Newcastle, NSW, Australia</p>

  <div class="room-photo" role="img" aria-label="Photo of a modern living room with a wall-mounted flat screen TV and home cinema speakers"></div>
  <p class="photo-caption">We are trying to target areas where there has been a new transmitter installed and most houses just require their aerial redirecting and tv's retuning.</p>

  <ul class="perks">
    <li>Free 5 Year Warranty</li>
    <li>Free Signal Testing</li>
    <li>Free Onsite Quote</li>
  </ul>
</main>
</body>
</html>
```